1 page A4 double sided Brochure Design Folded to envelope size. Interesting fold design would be co

Small family run guesthouse BnB in Blue Mountains Australia needs a new brochure showing different aspects of business

We need a new brochure to go with our new website. Basically the design would be good as a double sided brochure that can be folded down to standard envelope size.

We have seen a few interesting brochure designs before that fold in different ways (and therefore have the design to match) but still fold down to this size to help with postage.

The design would have to showcase the different aspects of our business including individual accommodation for couples and families, conference market, wedding market, retreat market and events market (parties, re-unions etc). The Business must be Showcased as The Fernhollow Lodge, Blue Mountains

It is possible to arrange design so folds separate different sections of info/pictures.

It is also optional that we possibly have 2 brochures instead, one that is a basic all inclusive once described and one that only deals with group bookings (wedding conference retreats etc etc)

Must match design elements from our web page. Feel free to take informations, elements and images from there for design www.fernhollowlodge.com.au

Here is a link to our view we wake up to every morning to inspire all those working on a design!
http://www.fernhollowlodge.com.au/images/view.jpg

Target Market(s)

Group bookings, weddings, conferences, retreats, events and Blue Mountains Travellers

Industry/Entity Type

Accommodation

Requirements
Must have
• Must be based on our current websites design feel, colours, etc
Must be showcased as The Fernhollow Lodge Blue Mountains.
Must mention The Blue Mountains as a world heritage destination
Must be A4 double sided that can fold down to 1/3 the size to fit into a standard envelope. Any designs that will not fit in a standard envelope once folded can not be accepted as they are outside the brief
Nice to have
• Interesting folding design to get people interested to read it.

```html
<!DOCTYPE html>
<html lang="en">
<head>
<meta charset="utf-8">
<title>The Fernhollow Lodge – Brochure</title>
<link rel="stylesheet" href="https://fonts.googleapis.com/css2?family=Josefin+Sans:wght@300;400;600&family=Marcellus&display=swap">
<style>
:root{
  --paper:#ffffff;
  --panel:#231f20;
  --ink:#e6dcc0;
  --ink-soft:#cfc6ad;
  --rule:#b9ae8c;
  --tab-top:#f4f2ea;
  --tab-bottom:#8d887a;
}
*{margin:0;padding:0;box-sizing:border-box}
html,body{width:845px;height:1200px;overflow:hidden;background:var(--paper)}
body{position:relative;font-family:"Josefin Sans",sans-serif;font-weight:300;color:var(--ink)}
.panel{position:absolute;left:17px;width:811px;background:var(--panel)}
.panel--outer{top:17px;height:575px}
.panel--inner{top:609px;height:576px}
.abs{position:absolute}
.address{top:38px;left:230px;width:390px;text-align:center;font-size:12.5px;line-height:15px;letter-spacing:.3px}
.brand{top:43px;left:627px;width:98px;height:121px;background:#3a3532;display:flex;flex-direction:column;justify-content:flex-end;align-items:center;padding-bottom:8px;text-align:center}
.brand__name{font-family:"Marcellus",serif;font-size:11px;color:var(--ink);letter-spacing:.5px}
.brand__phone{font-size:9px;margin-top:3px}
.brand__tag{font-size:5.5px;margin-top:3px;letter-spacing:.3px;line-height:7px}
.textbox{border:1px solid var(--rule)}
.intro{top:108px;left:21px;width:230px;height:361px;padding:14px 10px;font-size:7.4px;line-height:8.6px;text-align:right;color:var(--ink-soft)}
.intro p{margin-bottom:9px}
.photo{background:linear-gradient(180deg,#dfe8ee 0%,#9fb0a0 30%,#4f6a35 60%,#2e3b1f 100%)}
.photo--view{top:108px;left:271px;width:540px;height:361px}
.photo--falls{top:0;left:542px;width:269px;height:576px;background:linear-gradient(180deg,#c9d9a8 0%,#5b7a36 30%,#6b5a45 55%,#dfe2dc 70%,#3d3a30 100%)}
.contact{top:500px;left:230px;width:390px;text-align:center;font-size:12.5px;line-height:15px}
.headline{top:503px;left:560px;width:240px;text-align:center;font-family:"Marcellus",serif;font-size:16px;line-height:19px}
.section{top:108px;width:231px;height:357px;padding:0 12px}
.section--property{left:21px}
.section--packages{left:290px}
.tab{margin:14px 4px 36px;height:27px;border-radius:3px;background:linear-gradient(180deg,var(--tab-top),var(--tab-bottom));color:#ffffff;text-shadow:0 0 2px #555;font-family:"Marcellus",serif;font-size:20px;text-align:center;line-height:28px}
.section p{font-size:7.4px;line-height:8.6px;margin-bottom:9px;color:var(--ink-soft)}
.package h3{font-weight:600;font-size:10px;color:var(--ink);margin-bottom:1px}
.package p{margin-bottom:12px}
.footer{top:505px;left:17px;width:510px;text-align:center;font-size:10.5px;line-height:13px}
</style>
</head>
<body>

<section class="panel panel--outer">
  <p class="abs address">18-22 Banksia Parade<br>Wentworth Falls NSW 2782 Australia</p>

  <div class="abs intro textbox">
    <p>The world heritage listed Blue Mountains area consists of 1.03 million ha of sandstone plateaux, escarpments and gorges dominated by temperate eucalypt forest.</p>
    <p>This magnificent, awe inspiring beauty makes the Blue Mountains one of the most important protected areas and assets of Australia and in fact the world. Along with the simple astounding beauty of the area the endangered and protected flora and fauna make it a must see location for most people and also a peaceful, serene place to escape the real world and experience a different one like no other.</p>
    <p>In that spirit The Fernhollow Lodge is a very special, personal, peaceful choice for your Blue Mountains accommodation. Being located on 32 acres of mostly virgin bushland, including endangered hanging swamp, backing onto national parkland, The Fernhollow Lodge allows you to experience the Blue Mountains in its true splendour.</p>
    <p>Being only 900 meters from the peaceful village of Wentworth Falls however also places you in the heart of the Blue Mountains. Close to all its major attractions, lookouts, the Wentworth Falls lake and being in Wentworth Falls also leaves you close to some of the most spectacular walks and views on earth. You can experience everything the mountains have to offer with the astounding National Pass walk or even walk in the footsteps of the early naturalists all the way to the majesty of the waterfalls of Wentworth Falls.</p>
    <p>So close by... but worlds away</p>
  </div>

  <div class="abs photo photo--view" role="img" aria-label="Photograph of the bushland view across the Blue Mountains valley from the lodge lookout"></div>

  <div class="abs brand">
    <span class="brand__name">The Fernhollow</span>
    <span class="brand__phone">02 4759 3186</span>
    <span class="brand__tag">RETREATS · GROUP STAYS<br>CONFERENCES · EVENTS</span>
  </div>

  <p class="abs contact">www.fernhollowlodge.com.au<br>Phone : 02 4759 3186<br>info@fernhollowlodge.com.au</p>
  <p class="abs headline">The Blue Mountains<br>as a world heritage destination</p>
</section>

<section class="panel panel--inner">
  <div class="abs section section--property textbox">
    <h2 class="tab">The Property</h2>
    <p>The Fernhollow Lodge Blue Mountains is a small family run guesthouse, bush retreat and function centre.</p>
    <p>Located on 32 acres of pristine virgin bushland in the centre of world heritage listed national park land The Fernhollow Lodge is your perfect Blue Mountains accommodation whether you are looking for a quiet place to escape with someone special or a function or conference venue in the Blue Mountains for your next group escape or private, personal, specially tailored wedding.</p>
    <p>The Fernhollow Lodge has 2 buildings. The main retreat with 20 well appointed en suited rooms, each with views across the pool and valley, along with 2 function rooms, games room, commercial kitchen, pool and outdoor BBQ area.<br>The second is our manor house, a large, simple 7 bedroom, 4 bathroom house with lounge kitchen and dining room.</p>
    <p>Together with our private, friendly, family run atmosphere The Fernhollow Lodge is the perfect place to escape the real world and explore another.</p>
    <p>So close by... but worlds away</p>
    <p>Wattle Cottage is our smaller sister property in Katoomba perfect for families and small groups</p>
  </div>

  <div class="abs section section--packages textbox">
    <h2 class="tab">Our Packages</h2>
    <div class="package">
      <h3>Conference</h3>
      <p>The Fernhollow Lodge prides itself as the venue of choice for many of the worlds best companies for their conference needs.<br>Between our main retreat, the manor house and Wattle Cottage we have various configurations available for any style or number for your next Blue Mountains conference from 8 attendees up to 50 (accommodated all in separate beds).</p>
    </div>
    <div class="package">
      <h3>Weddings</h3>
      <p>The Fernhollow Lodge is the perfect, private, flexible venue for your special day.</p>
    </div>
    <div class="package">
      <h3>Retreats</h3>
      <p>A true retreat requires something special to really let go of the outside world and focus on that which is truely important.</p>
    </div>
    <div class="package">
      <h3>Events</h3>
      <p>Reunions, birthdays, church groups, parties, family get togethers and more The Fernhollow Lodge Blue Mountains is the perfect function venue to get together and really leave the world behind whilst re-connecting with your friends and family.</p>
    </div>
  </div>

  <div class="abs photo photo--falls" role="img" aria-label="Photograph of a waterfall cascading over sandstone rocks in green bushland"></div>

  <p class="abs footer">Family owned and run Blue Mountains accommodation, retreat, conference, wedding and function<br>centre set on 32 acres of virgin bushland in the beauty of a world heritage location.</p>
</section>

</body>
</html>
```